Trailer wrap for home remodeling company in Sarasota County Florida

I need a wrap design for an enclosed trailer. I like the idea of adding a picture of a really nice kitchen or bathroom, possibly a before and after.
Matte black background
Must include the below information
Pinecrest Home Remodeling
CGC2871093
941-555–0184
www.pinecresthomeremodeling.example
Bathrooms,Kitchens, Additions, Remodels
Trusted Expertise. Refined Design
Trailer is currently all black
Updates

Designs are not what we are looking for, very busy

Industry/Entity Type

Home Remodeling

Colors
0054AA
0677BA
7BADD7
CADEEF
E8F1F8

Requirements
Must have
• Matte black background

```html
<!DOCTYPE html>
<html lang="en">
<head>
<meta charset="utf-8">
<title>Pinecrest Home Remodeling – Trailer Wrap</title>
<link rel="stylesheet" href="https://fonts.googleapis.com/css2?family=Cinzel:wght@400&family=Open+Sans:wght@400;700&display=swap">
<style>
  :root {
    --canvas: #ffffff;
    --wrap-black: #000000;
    --blue-deep: #0054aa;
    --blue-bright: #1a6fe0;
    --blue-glow: #0b5bd3;
    --blue-night: #031a3d;
    --stripe-dark: #0a2a60;
    --text-white: #ffffff;
  }
  html, body {
    margin: 0;
    padding: 0;
    width: 1132px;
    height: 1200px;
    overflow: hidden;
    background: var(--canvas);
  }
  .canvas {
    position: relative;
    width: 1132px;
    height: 1200px;
  }
  .wrap-panel {
    position: absolute;
    left: 20px;
    top: 320px;
    width: 1092px;
    height: 560px;
    display: block;
  }
  .brand-name {
    font-family: "Cinzel", serif;
    font-weight: 400;
    fill: var(--text-white);
    letter-spacing: 3px;
  }
  .phone {
    font-family: "Open Sans", sans-serif;
    font-weight: 700;
    fill: var(--text-white);
    letter-spacing: -0.5px;
  }
  .website {
    font-family: "Open Sans", sans-serif;
    font-weight: 400;
    fill: var(--text-white);
  }
</style>
</head>
<body>
<main class="canvas">
  <svg class="wrap-panel" viewBox="0 0 874 448" xmlns="http://www.w3.org/2000/svg" aria-label="Trailer wrap side panel">
    <defs>
      <radialGradient id="panel-glow" cx="0.22" cy="0.2" r="0.8">
        <stop offset="0" stop-color="var(--blue-glow)"/>
        <stop offset="0.35" stop-color="var(--blue-deep)"/>
        <stop offset="0.68" stop-color="var(--blue-night)"/>
        <stop offset="1" stop-color="var(--wrap-black)"/>
      </radialGradient>
      <linearGradient id="stripe-fade" x1="0" x2="1" y1="0" y2="0">
        <stop offset="0" stop-color="var(--stripe-dark)"/>
        <stop offset="0.55" stop-color="var(--blue-deep)"/>
        <stop offset="1" stop-color="var(--blue-bright)"/>
      </linearGradient>
    </defs>

    <!-- panel background -->
    <rect class="panel-bg" width="874" height="448" fill="var(--wrap-black)"/>
    <rect class="panel-glow" width="874" height="448" fill="url(#panel-glow)"/>

    <!-- house line art areas -->
    <rect class="house-art house-art--left" x="0" y="190" width="190" height="170" fill="#0a3f8f" opacity="0.35" role="img" aria-label="Line drawing of a house gable with round window"/>
    <rect class="house-art house-art--right" x="665" y="225" width="90" height="95" fill="#0a3f8f" opacity="0.3" role="img" aria-label="Line drawing of a small house gable"/>

    <!-- diagonal accent bands -->
    <polygon class="diagonal-band" points="676,300 874,88 874,116 692,300" fill="var(--blue-bright)"/>
    <polygon class="diagonal-band diagonal-band--thin" points="650,312 840,110 846,110 656,312" fill="var(--blue-deep)" opacity="0.7"/>

    <!-- black info band -->
    <polygon class="info-band" points="0,312 705,312 660,360 0,360" fill="var(--wrap-black)"/>

    <!-- lower speed stripes -->
    <g class="speed-stripes" fill="url(#stripe-fade)">
      <polygon points="0,364 660,364 654,372 0,372"/>
      <polygon points="0,378 648,378 642,388 0,388"/>
      <polygon points="0,394 638,394 632,402 0,402"/>
      <polygon points="0,408 630,408 624,418 0,418"/>
      <polygon points="0,424 622,424 616,432 0,432"/>
      <polygon points="0,438 614,438 610,444 0,444"/>
    </g>

    <!-- brand name -->
    <text class="brand-name" x="442" y="150" text-anchor="middle" font-size="40">PINECREST HOME</text>
    <text class="brand-name" x="442" y="205" text-anchor="middle" font-size="40">REMODELING</text>

    <!-- contact -->
    <text class="phone" x="443" y="303" text-anchor="middle" font-size="40">941-555–0184</text>
    <text class="website" x="455" y="346" text-anchor="middle" font-size="26">www.pinecresthomeremodeling.example</text>
  </svg>
</main>
</body>
</html>
```